kmvalerohub website

I need a new homepage design for my current website at www.KMValeroHub.com. I want someone to look at my current website and develop a more appealing homepage... right now the colors don't blend very well and it needs a facelift

Reason: This has been extended to September 10th

```html
<!DOCTYPE html>
<html lang="en">
<head>
<meta charset="utf-8">
<title>KM Valero – Home</title>
<link rel="stylesheet" href="https://fonts.googleapis.com/css2?family=Great+Vibes&family=Open+Sans:wght@400;600&family=Roboto+Condensed:wght@400;700&family=EB+Garamond:wght@400;500&display=swap">
<style>
:root{
  --pink:#d8127a;
  --pink-dark:#a30c58;
  --pink-btn:#e0197f;
  --green:#1e9b3a;
  --text:#555;
  --line:#d6d6d6;
  --footer:#262626;
  --white:#fff;
}
*{box-sizing:border-box;margin:0;padding:0}
html,body{width:1200px;height:2187px;overflow:hidden;background:var(--white);font-family:"Open Sans",sans-serif;color:var(--text)}
.page{position:relative;width:1200px;height:2187px}
.abs{position:absolute}
/* header */
.topbar{left:0;top:0;width:1200px;height:106px;background:var(--pink)}
.brand{left:134px;top:26px;font-family:"Great Vibes",cursive;font-size:40px;color:var(--white);word-spacing:6px}
.call{left:714px;top:26px;color:var(--white);font-family:"Roboto Condensed",sans-serif}
.call small{display:flex;align-items:center;gap:6px;font-size:15px;margin-left:8px}
.call strong{display:block;font-size:19px;margin-top:4px}
.social{display:flex;gap:9px}
.social span{width:33px;height:33px;border:2px solid var(--white);border-radius:50%}
.topbar .social{position:absolute;left:872px;top:38px}
.nav{left:0;top:106px;width:1200px;height:50px;background:var(--pink-dark);border-bottom:5px solid var(--white)}
.nav a{position:absolute;top:14px;transform:translateX(-50%);color:var(--white);text-decoration:none;font-family:"Roboto Condensed",sans-serif;font-size:15px;text-transform:uppercase}
/* hero */
.hero{left:0;top:163px;width:1200px;height:441px;background:linear-gradient(180deg,#b89aa4 0%,#c7a3b1 55%,#c9628e 100%)}
.hero-person{left:131px;top:163px;width:350px;height:441px;background:linear-gradient(180deg,#6b4e52,#1e1a1d 45%,#2a2226)}
.hero-text{left:480px;top:180px;width:630px;text-align:center;font-family:"Great Vibes",cursive;color:var(--white)}
.hero-text .l1{font-size:56px;line-height:90px}
.hero-text .l2{font-size:62px;line-height:96px;color:var(--pink)}
.hero-text .l3{font-size:60px;line-height:104px}
.hero-btn{left:700px;top:490px;width:138px;height:45px;background:#5a4b50;border:1px solid #bfb2b6;border-radius:3px;color:var(--white);font-style:italic;font-size:16px;display:flex;align-items:center;justify-content:center}
.dots{left:572px;top:570px;display:flex;gap:3px}
.dots span{width:16px;height:16px;border-radius:50%;border:2px solid var(--white);background:var(--pink)}
.dots span:first-child{background:#3a2a30}
/* about */
.section-script{font-family:"Great Vibes",cursive;color:var(--pink);font-size:38px;word-spacing:4px}
.video{left:131px;top:706px;width:322px;height:229px;background:linear-gradient(135deg,#8a7a6a,#c9b9a4 60%,#6c5c50)}
.play{left:247px;top:775px;width:92px;height:92px}
.about-text{left:499px;top:705px;width:566px;font-size:13px;line-height:27px}
.btn{background:var(--pink-btn);color:var(--white);font-size:15px;display:flex;align-items:center;justify-content:center;border-radius:2px}
.rule{left:131px;width:938px;border-top:1px dashed var(--line)}
/* products */
.h-sans{color:var(--pink);font-size:18px}
.arrow{width:19px;height:16px;background:#b4b4b4}
.product{width:208px}
.product .cover{height:170px;border:1px solid var(--line);display:flex;align-items:center;justify-content:center}
.product .cover div{width:80px;height:130px}
.product h3{font-weight:400;font-size:15px;line-height:20px;color:var(--pink);margin-top:18px}
.product p{font-size:11.5px;line-height:23px;margin-top:12px;color:#444}
.product p a{color:var(--green);font-size:13.5px;text-decoration:none}
/* lower */
.serif-title{font-family:"EB Garamond",serif;color:var(--pink);font-size:19px}
.checks{left:136px;top:1494px;width:300px;list-style:none;font-size:11.5px;color:#444}
.checks li{position:relative;padding-left:28px;line-height:18px;margin-bottom:14px}
.checks li svg{position:absolute;left:2px;top:2px}
.news{left:456px;width:280px;height:102px;border-bottom:1px solid var(--line)}
.news .thumb{position:absolute;left:0;top:0;width:69px;height:70px;background:linear-gradient(135deg,#3b2a24,#a27c66 60%,#e6d8cf)}
.news h4{position:absolute;left:86px;top:0;font-family:"EB Garamond",serif;font-weight:400;color:var(--green);font-size:14.5px}
.news p{position:absolute;left:86px;top:24px;width:190px;font-family:"EB Garamond",serif;font-size:12.5px;line-height:19.5px;color:#444}
.report{left:768px;top:1424px;width:301px;height:407px;border:1px solid #cfcfcf;background:linear-gradient(180deg,#fff 0%,#fff 40%,#e8e8e8 100%)}
.report-head{height:72px;border-bottom:1px dashed #c7c7c7;display:flex;align-items:center;padding-left:58px;gap:20px}
.report-cover{width:38px;height:50px;background:linear-gradient(135deg,#2a4f96,#d8127a)}
.report-head strong{font-family:"Roboto Condensed",sans-serif;font-weight:400;color:var(--pink);font-size:19px}
.report p{position:absolute;left:24px;top:90px;width:258px;font-size:12px;line-height:21px;color:#444}
.field{width:249px;height:46px;border:1px solid #b5b5b5;border-radius:3px;background:linear-gradient(#fafafa,#ececec);font-size:12px;color:#555;padding:14px 12px}
.partners{left:131px;top:1898px;width:938px;height:139px;border:1px solid #e4e4e4;display:flex;align-items:center;justify-content:space-around;padding:0 16px}
.partners span{font-family:"Roboto Condensed",sans-serif;font-weight:700;font-size:22px;color:#7a7a7a}
/* footer */
.footer{left:0;top:2056px;width:1200px;height:131px;background:var(--footer);color:var(--white)}
.footer-links{position:absolute;left:131px;top:32px;font-size:11.5px;text-transform:uppercase;word-spacing:2px}
.footer-links i{font-style:normal;margin:0 9px}
.copy{position:absolute;left:131px;top:79px;font-size:11px}
.footer .social{position:absolute;left:872px;top:45px}
</style>
</head>
<body>
<div class="page">

<header class="abs topbar">
  <div class="abs brand">K M Valero</div>
  <div class="abs call">
    <small><svg width="12" height="16" viewBox="0 0 12 16"><path d="M3 1 L5 4 L4 6 Q5 9 7 11 L9 10 L11.5 12.5 L9.5 15 Q1 11 1 3 Z" fill="#fff"/></svg>Call Us Today</small>
    <strong>555-014-2290</strong>
  </div>
  <div class="social" role="img" aria-label="Social network links"><span></span><span></span><span></span><span></span><span></span></div>
</header>

<nav class="abs nav">
  <a style="left:182px">Home</a><a style="left:309px">Products</a><a style="left:439px">About</a><a style="left:553px">Blog</a><a style="left:666px">Forum</a><a style="left:805px">Media Room</a><a style="left:975px">Success Stories</a>
</nav>

<section>
  <div class="abs hero" role="img" aria-label="Soft pink meadow backdrop"></div>
  <div class="abs hero-person" role="img" aria-label="Portrait of KM Valero in a black dress"></div>
  <div class="abs hero-text">
    <div class="l1">Discover</div>
    <div class="l2">Secrets To a SlimmerSexier</div>
    <div class="l3">&amp;Helthier You !</div>
  </div>
  <div class="abs hero-btn">Learn More</div>
  <div class="abs dots"><span></span><span></span><span></span></div>
</section>

<section>
  <h2 class="abs section-script" style="left:131px;top:628px;font-weight:400">About K M Valero !</h2>
  <div class="abs video" role="img" aria-label="Video still of KM Valero speaking at home"></div>
  <svg class="abs play" viewBox="0 0 92 92"><circle cx="46" cy="46" r="27" fill="rgba(255,255,255,.25)" stroke="#fff" stroke-width="3"/><path d="M38 32 L62 46 L38 60 Z" fill="#fff"/></svg>
  <p class="abs about-text">KM Valero is a nutritionist and certified weight-loss expert, passionate relationship/life coach, and inspirational speaker. She has been featured on The Daybreak Table Show, The Marlow Hayes Show, The Rowan Pike Show, and The Carter Lane Show.Get to know KM better through the pictures in her portfolio and at events and book signings. She shares images of her public appearances and candid photos from her day-to-day life.KM Valero is a nutritionist and certified weight-loss Daybreak Table Show, The Marlow Hayes Show...........</p>
  <div class="abs btn" style="left:502px;top:886px;width:118px;height:40px">Read More</div>
  <div class="abs rule" style="top:970px"></div>
</section>

<section>
  <h2 class="abs h-sans" style="left:131px;top:993px;font-weight:400">Our Products</h2>
  <svg class="abs arrow" style="left:1022px;top:994px" viewBox="0 0 19 16"><path d="M13 8 H6 M9 5 L6 8 L9 11" stroke="#fff" stroke-width="1.5" fill="none"/></svg>
  <svg class="abs arrow" style="left:1047px;top:994px" viewBox="0 0 19 16"><path d="M6 8 H13 M10 5 L13 8 L10 11" stroke="#fff" stroke-width="1.5" fill="none"/></svg>
  <article class="abs product" style="left:133px;top:1035px"><div class="cover"><div role="img" aria-label="Green smoothie book cover" style="background:linear-gradient(135deg,#c7e07a,#3f8f2c)"></div></div><h3>The 10-Day Green Blend Reset</h3><p>The 10-Day Green Blend Reset will jump-start your weight loss, increase your energy level, clear your your overall health...... <a>Read More</a></p></article>
  <article class="abs product" style="left:376px;top:1035px"><div class="cover"><div role="img" aria-label="Weight loss book cover" style="background:linear-gradient(135deg,#f4b6d2,#d8127a)"></div></div><h3>The 10-Day Green Blend Reset</h3><p>The 10-Day Green Blend Reset will jump-start your weight loss, increase your energy level, clear your your overall health...... <a>Read More</a></p></article>
  <article class="abs product" style="left:618px;top:1035px"><div class="cover"><div role="img" aria-label="Belly fat book cover" style="background:linear-gradient(135deg,#f0f0f0,#c8322f 60%,#2a4f96)"></div></div><h3>The 10-Day Green Blend Reset</h3><p>The 10-Day Green Blend Reset will jump-start your weight loss, increase your energy level, clear your your overall health...... <a>Read More</a></p></article>
  <article class="abs product" style="left:859px;top:1035px"><div class="cover"><div role="img" aria-label="Program box set with discs" style="width:110px;height:120px;background:linear-gradient(135deg,#e9e9e9,#d77aa8)"></div></div><h3>The 10-Day Green Blend Reset</h3><p>The 10-Day Green Blend Reset will jump-start your weight loss, increase your energy level, clear your your overall health...... <a>Read More</a></p></article>
  <div class="abs rule" style="top:1401px"></div>
</section>

<section>
  <h2 class="abs serif-title" style="left:136px;top:1433px;font-weight:400">The 10-Day Green Blend Reset</h2>
  <ul class="abs checks">
    <li><svg width="13" height="11" viewBox="0 0 13 11"><path d="M1 6 L5 10 L12 1" stroke="var(--green)" stroke-width="2" fill="none"/></svg>Lose 10-15 pounds in 10 days</li>
    <li><svg width="13" height="11" viewBox="0 0 13 11"><path d="M1 6 L5 10 L12 1" stroke="var(--green)" stroke-width="2" fill="none"/></svg>Get rid of stubborn body fat,including belly fat</li>
    <li><svg width="13" height="11" viewBox="0 0 13 11"><path d="M1 6 L5 10 L12 1" stroke="var(--green)" stroke-width="2" fill="none"/></svg>Drop pounds and without grueling workouts</li>
    <li><svg width="13" height="11" viewBox="0 0 13 11"><path d="M1 6 L5 10 L12 1" stroke="var(--green)" stroke-width="2" fill="none"/></svg>Learn to live a healthier lifestyle of &nbsp;healthy eating</li>
    <li><svg width="13" height="11" viewBox="0 0 13 11"><path d="M1 6 L5 10 L12 1" stroke="var(--green)" stroke-width="2" fill="none"/></svg>Help your body naturally crave healthy foods so you never have to diet again</li>
    <li><svg width="13" height="11" viewBox="0 0 13 11"><path d="M1 6 L5 10 L12 1" stroke="var(--green)" stroke-width="2" fill="none"/></svg>Receive over 100 green smoothie recipes for various health conditions and goals</li>
    <li><svg width="13" height="11" viewBox="0 0 13 11"><path d="M1 6 L5 10 L12 1" stroke="var(--green)" stroke-width="2" fill="none"/></svg>Lose 10-15 pounds in 10 days</li>
    <li><svg width="13" height="11" viewBox="0 0 13 11"><path d="M1 6 L5 10 L12 1" stroke="var(--green)" stroke-width="2" fill="none"/></svg>Get rid of stubborn body fat,including belly fat</li>
    <li><svg width="13" height="11" viewBox="0 0 13 11"><path d="M1 6 L5 10 L12 1" stroke="var(--green)" stroke-width="2" fill="none"/></svg>Drop pounds and without grueling workouts</li>
  </ul>

  <h2 class="abs serif-title" style="left:468px;top:1433px;font-weight:400">News &amp; Events</h2>
  <article class="abs news" style="top:1484px"><div class="thumb" role="img" aria-label="Photo of KM Valero at a radio studio"></div><h4>The TV and Radio Personality</h4><p>KM's expertise has been featured on The Daybreak Table Show, The Marlow Hayes Show,...</p></article>
  <article class="abs news" style="top:1606px"><div class="thumb" role="img" aria-label="Photo of KM Valero with a guest"></div><h4>The TV and Radio Personality</h4><p>KM's expertise has been featured on The Daybreak Table Show, The Marlow Hayes Show,...</p></article>
  <article class="abs news" style="top:1731px"><div class="thumb" role="img" aria-label="Portrait of KM Valero smiling"></div><h4>The TV and Radio Personality</h4><p>KM's expertise has been featured on The Daybreak Table Show, The Marlow Hayes Show,...</p></article>

  <aside class="abs report">
    <div class="report-head"><div class="report-cover" role="img" aria-label="Free report cover"></div><strong>FREE Report:</strong></div>
    <p>7 Habits Keeping Your Scale Stuck!"Just enter your name and email below to get instant to this 30 page report absolutely FREE!</p>
    <div class="abs field" style="left:26px;top:179px">Name :</div>
    <div class="abs field" style="left:26px;top:255px">Email :</div>
    <div class="abs btn" style="left:80px;top:329px;width:142px;height:46px;font-size:16px">SUBSCRIBE</div>
  </aside>
  <div class="abs rule" style="top:1871px"></div>
</section>

<section class="abs partners" aria-label="As featured on">
  <span>Tallowmere Post</span><span>Kestrel One</span><span>Quillby TV</span><span>Orrinwave Radio</span><span>Vantry Net</span><span>Lumelle Daily</span>
</section>

<footer class="abs footer">
  <div class="footer-links">Home<i>/</i>Products<i>/</i>About<i>/</i>Blog<i>/</i>Forum<i>/</i>Media Room<i>/</i>Success Stories</div>
  <div class="copy">Copyright 2014 Bluepeak Studio.All Right Reseved.</div>
  <div class="social" role="img" aria-label="Social network links"><span></span><span></span><span></span><span></span><span></span></div>
</footer>

</div>
</body>
</html>
```